SkyvornQ Business Cards and Stationary Design

Need a design for our business cards and stationary. I want to carry on the theme of the logo. I want the business cards to have a design on the back. I would like the business cards and the stationary to carry the same theme, design scheme, and branding

Target Market(s)

Airlines and Maintenance Facilities

Industry/Entity Type

Aviation

Contact Information for Business Card

Name
Position Title
Address: 4827 Trellis Hollow Road, Marrowgate, Ostrela, 00417
Office Number
Mobile Number
Email
Website

Font styles to use
Serif
Sans Serif

Colors

Designer to choose colors to be used in the design.

```html
<!DOCTYPE html>
<html lang="en">
<head>
<meta charset="utf-8">
<title>SkyvornQ Business Card</title>
<link href="https://fonts.googleapis.com/css2?family=Open+Sans:wght@400;600;700&display=swap" rel="stylesheet">
<style>
  :root {
    --navy: #0b3170;
    --navy-deep: #082a5e;
    --navy-band: #0a2d66;
    --navy-line: #1d4384;
    --edge: #0d2f63;
    --paper: #f7f8fa;
    --ink-light: #ffffff;
    --blue-mark: #1e78d2;
    --fold: #9aa3b0;
    --stage: #2b2c2f;
  }
  * { margin: 0; padding: 0; box-sizing: border-box; }
  html, body { width: 1200px; height: 900px; overflow: hidden; }
  body {
    background: var(--stage);
    font-family: "Open Sans", Arial, sans-serif;
    position: relative;
  }
  .card {
    position: absolute;
    left: 250px;
    width: 700px;
    height: 400px;
    border-radius: 22px;
    overflow: hidden;
  }
  .card-front { top: 30px; background: var(--navy); }
  .card-back { top: 470px; background: var(--navy); }

  /* front */
  .front-edge {
    position: absolute; left: 0; top: 0; bottom: 0; width: 26px;
    background: var(--edge);
  }
  .front-brand-panel {
    position: absolute; left: 26px; top: 0; bottom: 0; width: 250px;
    background: var(--paper);
    display: flex; align-items: center; justify-content: center; gap: 12px;
  }
  .brand-dot {
    width: 26px; height: 26px; border-radius: 50%;
    background: var(--blue-mark);
  }
  .brand-name-front {
    font-weight: 700; font-size: 32px; color: var(--blue-mark);
  }
  .front-info {
    position: absolute; left: 276px; top: 0; right: 0; bottom: 0;
  }
  .band {
    position: absolute; left: 0; right: 0;
    border-bottom: 1px solid var(--navy-line);
  }
  .band-name { top: 0; height: 100px; background: var(--navy-deep); }
  .band-row { height: 46px; background: var(--navy-band); }
  .band-row.r1 { top: 100px; }
  .band-row.r2 { top: 146px; background: var(--navy-deep); }
  .band-row.r3 { top: 192px; }
  .band-row.r4 { top: 238px; background: var(--navy-deep); }
  .band-address { top: 284px; bottom: 0; background: var(--navy); border: 0; }
  .person-name {
    position: absolute; left: 50px; top: 38px;
    font-weight: 700; font-size: 24px; color: var(--ink-light);
  }
  .person-title {
    position: absolute; left: 62px; top: 70px;
    font-size: 14px; color: var(--ink-light);
  }
  .contact {
    position: absolute; left: 50px;
    display: flex; align-items: center; gap: 14px;
    height: 46px; color: var(--ink-light); font-size: 18px;
  }
  .contact svg { width: 20px; height: 20px; fill: var(--ink-light); }
  .c1 { top: 100px; } .c2 { top: 146px; } .c3 { top: 192px; } .c4 { top: 238px; }
  .address {
    position: absolute; left: 80px; top: 306px;
    font-size: 18px; line-height: 28px; color: var(--ink-light);
  }
  .fold {
    position: absolute; left: 262px; width: 14px; height: 22px;
    background: var(--fold);
    clip-path: polygon(100% 0, 100% 100%, 0 100%);
  }
  .fold-top { top: 78px; }
  .fold-bottom { top: 284px; }

  /* back */
  .back-brand {
    position: absolute; left: 0; right: 0; top: 150px;
    display: flex; align-items: center; justify-content: center; gap: 20px;
  }
  .brand-ring {
    width: 56px; height: 56px; border-radius: 50%;
    background: var(--ink-light);
  }
  .brand-name-back {
    font-weight: 700; font-size: 58px; letter-spacing: 10px;
    color: var(--ink-light);
  }
  .back-web {
    position: absolute; left: 0; right: 0; top: 270px;
    display: flex; align-items: center; justify-content: center; gap: 16px;
    color: var(--ink-light); font-size: 18px;
  }
  .back-web .rule { width: 40px; height: 1px; background: var(--ink-light); }
</style>
</head>
<body>
  <section class="card card-front">
    <div class="front-edge"></div>
    <div class="front-brand-panel">
      <span class="brand-dot"></span>
      <span class="brand-name-front">SkyvornQ</span>
    </div>
    <div class="front-info">
      <div class="band band-name"></div>
      <div class="band band-row r1"></div>
      <div class="band band-row r2"></div>
      <div class="band band-row r3"></div>
      <div class="band band-row r4"></div>
      <div class="band band-address"></div>

      <p class="person-name">Dara Holloway</p>
      <p class="person-title">President</p>

      <div class="contact c1">
        <svg viewBox="0 0 24 24"><path d="M6.6 10.8a15.1 15.1 0 0 0 6.6 6.6l2.2-2.2a1 1 0 0 1 1-.25 11.4 11.4 0 0 0 3.6.57 1 1 0 0 1 1 1V20a1 1 0 0 1-1 1A17 17 0 0 1 3 4a1 1 0 0 1 1-1h3.5a1 1 0 0 1 1 1c0 1.25.2 2.45.57 3.57a1 1 0 0 1-.25 1z"/></svg>
        <span>(555) 318-2047</span>
      </div>
      <div class="contact c2">
        <svg viewBox="0 0 24 24"><path d="M7 3h8l2 2v4H7z M4 10h16a1 1 0 0 1 1 1v6a1 1 0 0 1-1 1h-3v3H7v-3H4a1 1 0 0 1-1-1v-6a1 1 0 0 1 1-1z M9 16v3h6v-3z"/></svg>
        <span>(555) 318-2048</span>
      </div>
      <div class="contact c3">
        <svg viewBox="0 0 24 24"><path d="M2 5h20v14H2z M4 7v.4l8 5.2 8-5.2V7z"/></svg>
        <span>info@skyvornq.com</span>
      </div>
      <div class="contact c4">
        <svg viewBox="0 0 24 24"><path d="M12 2a10 10 0 1 0 0 20 10 10 0 0 0 0-20zm6.9 9h-3a15 15 0 0 0-1.3-5.9A8 8 0 0 1 18.9 11zM12 4.1c.9 1.2 1.7 3.6 1.9 6.9h-3.8c.2-3.3 1-5.7 1.9-6.9zM9.4 5.1A15 15 0 0 0 8.1 11h-3a8 8 0 0 1 4.3-5.9zM5.1 13h3a15 15 0 0 0 1.3 5.9A8 8 0 0 1 5.1 13zM12 19.9c-.9-1.2-1.7-3.6-1.9-6.9h3.8c-.2 3.3-1 5.7-1.9 6.9zm2.6-1a15 15 0 0 0 1.3-5.9h3a8 8 0 0 1-4.3 5.9z"/></svg>
        <span>www.skyvornq.com</span>
      </div>

      <p class="address">4827 Trellis Hollow Road,<br>Marrowgate, Ostrela, 00417</p>
    </div>
    <div class="fold fold-top"></div>
    <div class="fold fold-bottom"></div>
  </section>

  <section class="card card-back">
    <div class="back-brand">
      <span class="brand-ring"></span>
      <span class="brand-name-back">SKYVORNQ</span>
    </div>
    <div class="back-web">
      <span class="rule"></span>
      <span>www.skyvornq.com</span>
      <span class="rule"></span>
    </div>
  </section>
</body>
</html>
```